A multi-page brochure that explains our firm ,KVL Wealth Management

We have a current brochure attached but it is a compilation of several items combined into one. We would like this to have the same content but be one complete theme. We are a financial planning form so it needs to have a level of professionalism but also a comfortable approach for clients and showing that was have a lot of resources and experience. We cater mostly to the 55-60+ age community.

We need the front page picture changed. lake themed would be great, like our website www.TheMoskaHouse.com
Just to be clear we use KVL Wealth Management now as our company name. Parent company name is The Moska House LLC. I attached the current mock brochure and our new logos.
Our logo colors are:
KVL WM Logo Colors:

Blue:
HEX: #0f75bc
RGB: rgba(15,117,188,255)

Grey:
HEX: #6d6e71
RGB: rgba(109,110,113,255)

Target Market(s)

High-level individuals that are looking for financial guidance who are 40 years old and up

Industry/Entity Type

Wealth Management

Requirements
Must have
• Clean and crisp
Nice to have
• https://www.bramblestoneplanners.com/wealth-management-brochure , this is a sample we like

```html
<!DOCTYPE html>
<html lang="en">
<head>
<meta charset="utf-8">
<title>KVL Wealth Management Brochure Spread</title>
<link href="https://fonts.googleapis.com/css2?family=Archivo:wght@400;500;600;700;800;900&display=swap" rel="stylesheet">
<style>
  :root{
    --brand-blue:#1f63b5;
    --logo-blue:#0f75bc;
    --logo-grey:#6d6e71;
    --ink:#111418;
    --dark-band:#4a4b4f;
    --paper:#ffffff;
    --bg:#e9e4dc;
  }
  *{margin:0;padding:0;box-sizing:border-box}
  html,body{width:1200px;height:868px;overflow:hidden;background:var(--bg);font-family:"Archivo",Arial,sans-serif;color:var(--ink)}
  .spread{display:flex;width:1200px;height:868px}
  .page{position:relative;width:600px;height:868px;background:var(--paper);overflow:hidden}
  .page svg.art{position:absolute;inset:0;width:600px;height:868px}
  .brand-name{position:absolute;font-family:"Archivo",Arial,sans-serif;font-weight:600;color:var(--logo-blue);line-height:1.05;letter-spacing:.2px}

  /* back cover */
  .section-tag{position:absolute;left:26px;top:24px;display:flex;align-items:center;gap:8px;font-size:9px;font-weight:500}
  .section-tag::before{content:"";width:7px;height:7px;background:var(--ink)}
  .section-rule{position:absolute;left:161px;top:29px;width:170px;height:2px;background:var(--brand-blue)}
  .back .brand-name{left:26px;top:72px;font-size:30px;width:260px}
  .contact-title{position:absolute;left:31px;top:556px;font-size:24px;font-weight:600;color:var(--brand-blue)}
  .contact-item{position:absolute;display:flex;align-items:center;gap:10px;font-size:11px;font-weight:500;line-height:1.35}
  .icon{width:30px;height:30px;flex:none;border-radius:50%;background:var(--brand-blue);box-shadow:0 0 0 4px #e4ecf6;display:flex;align-items:center;justify-content:center}
  .icon svg{width:14px;height:14px}
  .contact-address{left:35px;top:602px}
  .contact-phone{left:290px;top:600px}
  .contact-web{left:35px;top:648px}
  .back-footer-name{position:absolute;left:28px;top:800px;font-size:13px;font-weight:600;color:#fff}
  .back-footer-rule{position:absolute;left:28px;top:825px;width:544px;height:1px;background:rgba(255,255,255,.7)}
  .disclaimer{position:absolute;left:28px;top:832px;width:560px;font-size:6.4px;line-height:1.4;color:#fff}

  /* front cover */
  .front .brand-name{left:37px;top:40px;font-size:34px;width:280px}
  .toll-free{position:absolute;left:416px;top:32px;display:flex;align-items:center;gap:10px}
  .toll-free .icon{background:#fff;box-shadow:0 0 0 3px rgba(255,255,255,.5)}
  .toll-free small{display:block;font-size:9px;font-weight:500;letter-spacing:.5px}
  .toll-free strong{display:block;font-size:15px;font-weight:700;letter-spacing:.3px}
  .headline{position:absolute;left:35px;top:602px}
  .headline .kicker{font-size:24px;font-weight:500;line-height:1.1}
  .headline .lead{font-size:45px;font-weight:900;color:var(--brand-blue);line-height:1.08;margin-top:10px;letter-spacing:-.3px}
  .headline .tail{font-size:34px;font-weight:800;line-height:1.1}
  .headline-rule{position:absolute;left:35px;top:740px;width:145px;height:3px;background:var(--brand-blue)}
  .parent-badge{position:absolute;left:35px;top:802px;width:154px;height:39px;background:var(--brand-blue);color:#fff;font-size:11px;display:flex;align-items:center;justify-content:center}
  .footer-rule{position:absolute;left:189px;top:822px;right:0;height:1px;background:var(--brand-blue)}
  .footer-web{position:absolute;left:246px;top:838px;font-size:11px;font-weight:500}
  .footer-offices{position:absolute;left:420px;top:836px;display:flex;align-items:center;gap:6px;font-size:8px;font-weight:500}
</style>
</head>
<body>
<main class="spread">

  <!-- Back cover -->
  <section class="page back">
    <svg class="art" viewBox="0 0 600 868" aria-hidden="true">
      <path d="M345 0 C390 82 500 108 600 82 V0 Z" fill="var(--brand-blue)"/>
      <path d="M382 0 C422 36 500 46 555 0 Z" fill="var(--ink)"/>
      <path d="M0 718 C120 700 250 758 380 800 C460 826 540 830 600 818 V868 H0 Z" fill="var(--brand-blue)"/>
      <path d="M355 790 C450 828 530 830 600 808 V820 C530 842 450 840 355 790 Z" fill="var(--ink)"/>
    </svg>
    <div class="section-tag">Wealth Management</div>
    <div class="section-rule"></div>
    <div class="brand-name">KVL Wealth Management</div>

    <h2 class="contact-title">Contact Info</h2>
    <div class="contact-item contact-address">
      <span class="icon"><svg viewBox="0 0 14 14"><path d="M7 1a4 4 0 0 0-4 4c0 3 4 8 4 8s4-5 4-8a4 4 0 0 0-4-4z" fill="#fff"/><circle cx="7" cy="5" r="1.5" fill="var(--brand-blue)"/></svg></span>
      <span>41 Harbor Crest Drive, Suite 210 |<br>Lakeview, MN 55390</span>
    </div>
    <div class="contact-item contact-phone">
      <span class="icon"><svg viewBox="0 0 14 14"><path d="M3 1.5l2 .2 1 3-1.3 1a7 7 0 0 0 3.6 3.6l1-1.3 3 1 .2 2c-.4.9-1.3 1.5-2.3 1.4C5.5 11.8 2.2 8.5 1.6 3.8 1.5 2.8 2.1 1.9 3 1.5z" fill="#fff"/></svg></span>
      <span>612.480.3157 |<br>877.410.2288</span>
    </div>
    <div class="contact-item contact-web">
      <span class="icon"><svg viewBox="0 0 14 14" fill="none" stroke="#fff" stroke-width="1.2"><circle cx="7" cy="7" r="5.5"/><ellipse cx="7" cy="7" rx="2.4" ry="5.5"/><path d="M1.5 7h11"/></svg></span>
      <span>www.TheMoskaHouse.com</span>
    </div>

    <div class="back-footer-name">KVL Wealth</div>
    <div class="back-footer-rule"></div>
    <p class="disclaimer">Securities and advisory services offered through Northpoint Advisory Network, Member FINRA/SIPC, a Registered Investment Adviser. Fixed insurance products and services offered through Harbor Insurance Agency or The Moska House.</p>
  </section>

  <!-- Front cover -->
  <section class="page front">
    <svg class="art" viewBox="0 0 600 868">
      <defs>
        <linearGradient id="lakeScene" x1="0" y1="0" x2="0" y2="1">
          <stop offset="0" stop-color="#cfe3f3"/>
          <stop offset=".35" stop-color="#eef4f8"/>
          <stop offset=".5" stop-color="#7f9a8a"/>
          <stop offset=".62" stop-color="#5fa7b4"/>
          <stop offset="1" stop-color="#4f8b7f"/>
        </linearGradient>
        <radialGradient id="mist" cx=".75" cy=".2" r=".6">
          <stop offset="0" stop-color="#e9ebee"/>
          <stop offset="1" stop-color="#fff" stop-opacity="0"/>
        </radialGradient>
      </defs>
      <rect x="150" y="560" width="450" height="230" fill="url(#mist)"/>
      <path role="img" aria-label="Photograph of a calm mountain lake with a wooden pier and trees along the shore" d="M0 0 H600 V470 C520 430 420 420 330 430 C240 440 170 540 100 545 C60 548 20 532 0 520 Z" fill="url(#lakeScene)"/>
      <path d="M90 546 C200 540 255 418 340 404 C430 390 520 418 600 468 V500 C520 462 430 450 360 468 C280 490 200 548 90 546 Z" fill="var(--brand-blue)"/>
      <path d="M600 478 V598 C560 556 470 520 375 512 C460 478 540 468 600 478 Z" fill="var(--dark-band)"/>
    </svg>

    <div class="brand-name">KVL Wealth Management</div>
    <div class="toll-free">
      <span class="icon"><svg viewBox="0 0 14 14"><path d="M3 1.5l2 .2 1 3-1.3 1a7 7 0 0 0 3.6 3.6l1-1.3 3 1 .2 2c-.4.9-1.3 1.5-2.3 1.4C5.5 11.8 2.2 8.5 1.6 3.8 1.5 2.8 2.1 1.9 3 1.5z" fill="var(--brand-blue)"/></svg></span>
      <span><small>TOLL-FREE</small><strong>877.410.2288</strong></span>
    </div>

    <div class="headline">
      <p class="kicker">Wealth Management</p>
      <h1 class="lead">Focused on Your</h1>
      <p class="tail">Needs and Vision</p>
    </div>
    <div class="headline-rule"></div>

    <div class="parent-badge">The Moska House LLC</div>
    <div class="footer-rule"></div>
    <div class="footer-web">www.TheMoskaHouse.com</div>
    <div class="footer-offices">
      <svg width="12" height="14" viewBox="0 0 14 14"><path d="M7 1a4 4 0 0 0-4 4c0 3 4 8 4 8s4-5 4-8a4 4 0 0 0-4-4z" fill="none" stroke="var(--brand-blue)" stroke-width="1.3"/><circle cx="7" cy="5" r="1.4" fill="var(--brand-blue)"/></svg>
      <span>Lakeside &amp; Bay Area Offices</span>
    </div>
  </section>

</main>
</body>
</html>
```